Plume Arc Website - Enabling Omni channel

Slogan : Enabling Omnichannel Sales

1. Sell products via multiple sale channels
2. Access our technology and services to get your products moving through new channels
3. Customise our mobile and web technology platforms to suit your supply chain.

Slogan: Plume arc – Innovating new business.

Use the content from these websites to create a new one
http://vorbankhq.com/
http://lorvane-designs.com/plumeArc02/

Target Market(s)

Business and Coporations who need mobile and web technology or services to increase product sales within their vertical industry. Our case studies show the industries we have worked in; namely: Retail, wholesale, online retail, motor and auto trade. Also have rich experience in Importing and Exporting.

Industry/Entity Type

Retail

Number of Pages Required

3 page

Font styles to use
Sans Serif

Colors
0255a3
ec1f27
9bcb3c
ffffff
0792cd
ffc214

Requirements
Must have
• Punchy headline home page with possible animations or unique and interesting images

```html
<!DOCTYPE html>
<html lang="en">
<head>
<meta charset="utf-8">
<title>Plume Arc – Innovating new business</title>
<link href="https://fonts.googleapis.com/css2?family=Raleway:wght@400;500;600&family=Open+Sans:ital,wght@0,400;0,600;1,400&display=swap" rel="stylesheet">
<style>
:root{
  --brand-blue:#0255a3;
  --sky:#0792cd;
  --sun:#ffc214;
  --leaf:#9bcb3c;
  --red:#ec1f27;
  --white:#ffffff;
  --ink:#4a4a4a;
  --footer:#2e3239;
  --footer-deep:#24272c;
  --footer-text:#d8dadd;
}
*{margin:0;padding:0;box-sizing:border-box}
html,body{width:1200px;height:3087px;overflow:hidden}
body{font-family:"Open Sans",Arial,sans-serif;color:var(--ink);background:var(--white);position:relative}
h1,h2,h3,.box-title{font-family:"Raleway",Arial,sans-serif;font-weight:400}
section,header,footer{position:absolute;left:0;width:1200px}

/* header */
.site-header{top:0;height:124px;background:var(--white)}
.brand{position:absolute;left:130px;top:30px}
.brand-name{font-family:"Raleway",sans-serif;font-weight:600;font-size:36px;color:var(--brand-blue);line-height:1}
.brand-tag{font-family:"Raleway",sans-serif;font-size:14px;color:#333;margin-top:8px;letter-spacing:.3px}
.main-nav{position:absolute;right:140px;top:52px;display:flex;gap:42px;font-size:13px;color:#444}
.main-nav .active{color:var(--sky)}

/* hero */
.hero{top:124px;height:444px;background:linear-gradient(135deg,#5d5248 0%,#8a7866 30%,#b6a792 55%,#6f6a66 80%,#3d3a3a 100%);text-align:center;color:var(--white)}
.hero::after{content:"";position:absolute;inset:0;background:rgba(20,20,25,.35)}
.hero-inner{position:relative;z-index:1;padding-top:160px}
.hero h1{font-size:38px;letter-spacing:.3px}
.hero p{font-size:15px;margin-top:14px}
.btn{display:inline-block;background:var(--brand-blue);color:var(--white);border-radius:4px;font-size:14px}
.hero .btn{margin-top:24px;padding:11px 22px;background:#0a5fb8}
.dots{position:absolute;left:0;right:0;top:396px;z-index:1;display:flex;justify-content:center;gap:12px}
.dots span{width:10px;height:10px;border-radius:50%;border:1.5px solid var(--white)}
.dots .on{background:var(--white)}

/* offer boxes */
.offers{top:568px;height:202px;display:flex}
.offer{flex:1;color:var(--white);text-align:center;padding-top:40px}
.offer svg{width:44px;height:44px}
.box-title{font-size:24px;line-height:29px;margin-top:12px}
.offer.brand-box{background:var(--sky)}
.offer.product-box{background:var(--sun)}
.offer.service-box{background:var(--leaf)}

/* welcome */
.welcome{top:770px;height:288px;text-align:center}
.welcome h2{font-size:34px;color:var(--brand-blue);margin-top:50px}
.welcome p{width:940px;margin:24px auto 0;font-size:12.5px;line-height:24px;color:#444}
.welcome .btn{margin-top:18px;padding:7px 16px;font-size:12px}

/* features */
.features{top:1058px;height:446px}
.features-text{position:absolute;left:0;top:0;width:614px;height:446px;background:var(--sky);color:var(--white);padding:66px 0 0 135px}
.features-text h2{font-size:34px}
.features-text p{width:400px;font-size:12px;line-height:23px;margin-top:22px}
.feature-list{list-style:none;margin-top:22px;font-size:11.5px;line-height:20.5px}
.feature-list li{padding-left:20px;position:relative}
.feature-list li::before{content:"";position:absolute;left:0;top:7px;border-left:5px solid var(--white);border-top:4px solid transparent;border-bottom:4px solid transparent}
.feature-photo{position:absolute;left:614px;top:0;width:586px;height:446px;background:linear-gradient(120deg,#c9d6dc 0%,#8c9aa3 35%,#5d6770 60%,#a9b6bd 100%)}

/* services */
.services{top:1504px;height:478px;text-align:center}
.services h2{font-size:34px;color:var(--brand-blue);margin-top:44px}
.service-grid{position:absolute;top:136px;left:130px;width:940px;display:flex;justify-content:space-between}
.service{width:272px}
.service-icon{width:114px;height:114px;border-radius:50%;margin:0 auto;display:flex;align-items:center;justify-content:center;border:1px solid #e6e6e6;color:var(--brand-blue)}
.service-icon.filled{background:var(--sky);border-color:var(--sky);color:var(--white)}
.service-icon svg{width:38px;height:38px}
.service h3{font-size:20px;color:var(--sky);margin-top:34px}
.service p{font-size:12px;line-height:21px;margin-top:16px;text-align:justify;text-align-last:center}

/* faq */
.faq{top:1982px;height:448px}
.faq-photo{position:absolute;left:0;top:0;width:562px;height:448px;background:linear-gradient(100deg,#e8eef4 0%,#a9bccb 30%,#6f8296 55%,#c6d3de 80%,#eef2f6 100%)}
.faq-panel{position:absolute;left:562px;top:0;width:638px;height:448px;background:var(--leaf);color:var(--white);padding:38px 58px 0 58px}
.faq-panel h2{font-size:32px}
.faq-item{display:flex;justify-content:space-between;align-items:center;font-family:"Raleway",sans-serif;font-size:19px}
.faq-item .sign{font-size:26px;font-weight:600;line-height:1}
.faq-open{margin-top:16px}
.faq-answer{font-size:11px;line-height:19px;margin:10px 0 18px;width:480px}
.faq-answer a{color:var(--brand-blue);text-decoration:underline}
.faq-item+.faq-item{margin-top:14px}

/* stories */
.stories{top:2430px;height:348px;text-align:center}
.stories h2{font-size:34px;color:var(--brand-blue);margin-top:48px}
.avatar{width:78px;height:78px;border-radius:50%;margin:18px auto 0;background:radial-gradient(circle at 50% 40%,#e9c7a8,#b77c4f 70%,#7e5232)}
.stories p{width:1060px;margin:28px auto 0;font-size:12.5px;line-height:23px}
.story-name{font-style:italic;color:var(--sky);font-size:12px;margin-top:18px}

/* footer */
.site-footer{top:2778px;height:247px;background:var(--footer);color:var(--footer-text)}
.footer-brand{position:absolute;left:130px;top:42px;font-family:"Raleway",sans-serif;font-weight:600;font-size:40px;color:#8b9098}
.socials{position:absolute;left:132px;top:152px;display:flex;gap:8px}
.socials span{width:32px;height:32px;border-radius:50%;border:1.5px solid #d0d2d6}
.footer-col{position:absolute;top:38px;font-size:11.5px}
.footer-col h3{font-size:15px;color:var(--white);margin-bottom:20px}
.quick-links{left:445px}
.quick-links li{list-style:none;line-height:20.5px}
.newsletter{left:630px}
.newsletter p{font-size:11px}
.email-field{width:196px;height:36px;background:#555a62;margin-top:18px;padding:10px 12px;font-size:11px;color:#e3e3e3}
.newsletter .btn{margin-top:22px;padding:7px 18px;font-size:11px;background:#0a5fb8}
.contact{left:905px}
.contact li{list-style:none;display:flex;gap:12px;margin-bottom:12px;line-height:16px}
.contact svg{width:14px;height:14px;flex:none;margin-top:1px;fill:var(--white)}
.contact a{color:var(--white);text-decoration:underline}
.copyright{top:3025px;height:62px;background:var(--footer-deep);color:#ddd;font-size:11px;text-align:center;line-height:62px}
</style>
</head>
<body>

<header class="site-header">
  <div class="brand">
    <div class="brand-name">Plume Arc</div>
    <div class="brand-tag">Innovating new business</div>
  </div>
  <nav class="main-nav">
    <span class="active">Home</span><span>About Us</span><span>Why Us..?</span><span>Case Studies</span><span>FAQs</span><span>Contact</span>
  </nav>
</header>

<section class="hero" role="img" aria-label="Team of colleagues collaborating around a laptop at a meeting table">
  <div class="hero-inner">
    <h1>We can position your products</h1>
    <p>Your brand, products and services are the lifeblood of your business</p>
    <span class="btn">Request Quote</span>
  </div>
  <div class="dots"><span></span><span class="on"></span><span></span></div>
</section>

<section class="offers">
  <div class="offer brand-box">
    <svg viewBox="0 0 24 24" fill="#fff"><path d="M2 3h8l11 11-7 7L3 10V3zm4 2.5a1.5 1.5 0 100 3 1.5 1.5 0 000-3z"/></svg>
    <div class="box-title">Are Your a<br>Brand</div>
  </div>
  <div class="offer product-box">
    <svg viewBox="0 0 24 24" fill="#fff"><path d="M3 7l9-4 9 4v10l-9 4-9-4V7zm2 1.5v7.2l6 2.7v-7.2L5 8.5zm14 0l-6 2.7v7.2l6-2.7V8.5z"/></svg>
    <div class="box-title">Do you have<br>Products</div>
  </div>
  <div class="offer service-box">
    <svg viewBox="0 0 24 24" fill="#fff"><path d="M1 3h4l1 3h16l-3 8H8l-1 2h13v2H5l2-4L4 5H1V3zm7 17a1.5 1.5 0 103 0 1.5 1.5 0 00-3 0zm9 0a1.5 1.5 0 103 0 1.5 1.5 0 00-3 0z"/></svg>
    <div class="box-title">Do You Offer a<br>Service</div>
  </div>
</section>

<section class="welcome">
  <h2>Welcome to Plume Arc</h2>
  <p>If any of these situations are what you need, you're not alone. Many suppliers and manufacturers face these challenges. Plume Arc can help you create a marketing and sales plan for your situation, often incorporating our existing in-store and factory direct model using the Kelvra supply chain.We've developed a range of solutions that can start revolutionising your business' supply chain process now. Or, we can help you make your custom software application, a reality.</p>
  <span class="btn">Read More</span>
</section>

<section class="features">
  <div class="features-text">
    <h2>Our Features</h2>
    <p>We've developed a range of solutions that can start revolutionising your business' supply chain process now. Or, we can help you make your custom software application, a reality.</p>
    <ul class="feature-list">
      <li>Product cataloguing</li>
      <li>Product listing</li>
      <li>Quoting</li>
      <li>Sales team catalogue and quoting<br>management</li>
      <li>E-Brochure creation</li>
      <li>Inventory management</li>
      <li>Warehouse scanning</li>
    </ul>
  </div>
  <div class="feature-photo" role="img" aria-label="Business people gathered around a presentation in a bright office"></div>
</section>

<section class="services">
  <h2>Our Service</h2>
  <div class="service-grid">
    <div class="service">
      <div class="service-icon filled"><svg viewBox="0 0 24 24" fill="currentColor"><path d="M7 2h10a1 1 0 011 1v18a1 1 0 01-1 1H7a1 1 0 01-1-1V3a1 1 0 011-1zm1 3v13h8V5H8zm4 14.2a.9.9 0 100 1.8.9.9 0 000-1.8z"/></svg></div>
      <h3>Custom App</h3>
      <p>Fashion-apparel brand, Plume Arc acquired the brand, intellectual property, stock and trading in June 2014. The brand consisted</p>
    </div>
    <div class="service">
      <div class="service-icon"><svg viewBox="0 0 24 24" fill="currentColor"><path d="M3 9h4l10-5v16L7 15H6l1 5H4l-1-5V9zm16 1h2v4h-2z"/></svg></div>
      <h3>Marketing</h3>
      <p>Fashion-apparel brand, Plume Arc acquired the brand, intellectual property, stock and trading in June 2014. The brand consisted</p>
    </div>
    <div class="service">
      <div class="service-icon"><svg viewBox="0 0 24 24" fill="currentColor"><path d="M1 3h4l1 3h16l-3 8H8l-1 2h13v2H5l2-4L4 5H1V3zm7 17a1.5 1.5 0 103 0 1.5 1.5 0 00-3 0zm9 0a1.5 1.5 0 103 0 1.5 1.5 0 00-3 0z"/></svg></div>
      <h3>Sales</h3>
      <p>Fashion-apparel brand, Plume Arc acquired the brand, intellectual property, stock and trading in June 2014. The brand consisted</p>
    </div>
  </div>
</section>

<section class="faq">
  <div class="faq-photo" role="img" aria-label="Motion-blurred commuters walking through a bright city concourse"></div>
  <div class="faq-panel">
    <h2>FAQ</h2>
    <div class="faq-item faq-open"><span>Commissioned Selling</span><span class="sign">&minus;</span></div>
    <p class="faq-answer">We sell your products on commission. We find the channels to market. We find tradition retailers, online and other outlets. Both locally and internationally. <a>Read More</a></p>
    <div class="faq-item"><span>Multi-channel selling</span><span class="sign">+</span></div>
    <div class="faq-item"><span>Managed or DIY web and Bazely stores</span><span class="sign">+</span></div>
    <div class="faq-item"><span>Managed web and Bazely stores</span><span class="sign">+</span></div>
    <div class="faq-item"><span>Export and retail management</span><span class="sign">+</span></div>
    <div class="faq-item"><span>Flash sales clearance and job lots</span><span class="sign">+</span></div>
  </div>
</section>

<section class="stories">
  <h2>Sucess Stories</h2>
  <div class="avatar" role="img" aria-label="Client portrait"></div>
  <p>Fashion-apparel brand, Plume Arc acquired the brand, intellectual property, stock and trading in June 2014. The brand consisted of 80 SKU's and sold off a website. In order to increase the sales, Norvell an American retailer assisted in the exporting of the product.</p>
  <div class="story-name">- Dana Morrow -</div>
</section>

<footer class="site-footer">
  <div class="footer-brand">Plume Arc</div>
  <div class="socials" aria-label="Social links"><span></span><span></span><span></span><span></span><span></span></div>
  <div class="footer-col quick-links">
    <h3>Quick Links</h3>
    <ul><li>Home</li><li>About Us</li><li>Why Us..?</li><li>Case Studies</li><li>FAQs</li><li>Contact</li></ul>
  </div>
  <div class="footer-col newsletter">
    <h3>Newsletter</h3>
    <p>Sign Up for Our Newsletter &amp; Promotion</p>
    <div class="email-field">Enter Your email Id</div>
    <span class="btn">Subscribe</span>
  </div>
  <div class="footer-col contact">
    <h3>Contact Us</h3>
    <ul>
      <li><svg viewBox="0 0 24 24"><path d="M6.6 10.8a15 15 0 006.6 6.6l2.2-2.2a1 1 0 011-.25 11.4 11.4 0 003.6.6 1 1 0 011 1V20a1 1 0 01-1 1A17 17 0 013 4a1 1 0 011-1h3.5a1 1 0 011 1c0 1.25.2 2.45.6 3.6a1 1 0 01-.25 1z"/></svg>(555) 014-2290</li>
      <li><svg viewBox="0 0 24 24"><path d="M6 3h12v5H6zM3 9h18v9h-3v3H6v-3H3zm5 7v3h8v-3z"/></svg>800-555-0147 FREE</li>
      <li><svg viewBox="0 0 24 24"><path d="M2 5h20v14H2zm2 2v.5l8 5 8-5V7z"/></svg><a>hello@plumearc.example</a></li>
      <li><svg viewBox="0 0 24 24"><path d="M12 2a7 7 0 017 7c0 5-7 13-7 13S5 14 5 9a7 7 0 017-7zm0 4.5a2.5 2.5 0 100 5 2.5 2.5 0 000-5z"/></svg>#2868 Lorem ipsum dolor sit<br>amet, consectetur</li>
    </ul>
  </div>
</footer>

<div class="copyright" style="position:absolute;left:0;width:1200px">Copyright © 2016 Plume Arc. All Right Reserved.</div>

</body>
</html>
```